VOR Exterior Coatings

double sided. the front i want the name of the business each word on a new line with the VOR being bigger. id like teal, black and white colors. the back i want my contact info. Flat, no gloss. Something professional and I want to feel the letters bump put of the card. if possible maybe a paint sprayer in corner. not a car paint spray. (no tank on top of gun)
no vehicle paint sprayers. that means no tank on top of the gun. doesn't have to have a sprayer. black/dark background on the front. white back ground on back with info

```html
<!DOCTYPE html>
<html lang="en">
<head>
<meta charset="utf-8">
<title>VOR Exterior Coatings – Business Cards</title>
<link rel="stylesheet" href="https://fonts.googleapis.com/css2?family=Montserrat:wght@400;500;800&display=swap">
<style>
  :root {
    --stage: #161616;
    --card-dark: #050505;
    --card-light: #f6f6f6;
    --teal: #148a8c;
    --teal-light: #1fa3a5;
    --white: #f4f4f4;
    --grey-text: #d6d6d6;
    --ink: #1c1c1c;
    --ink-soft: #4a4a4a;
    --emboss: #d3d3d3;
    --rule-dark: #3a3a3a;
    --rule-light: #cfcfcf;
  }
  * { box-sizing: border-box; margin: 0; padding: 0; }
  html, body { width: 1200px; height: 820px; overflow: hidden; }
  body {
    background: var(--stage);
    font-family: "Montserrat", Arial, sans-serif;
    position: relative;
  }
  .card {
    position: absolute;
    top: 255px;
    width: 540px;
    height: 309px;
    border: 1.5px solid var(--teal);
    overflow: hidden;
  }
  .card--front { left: 40px; background: var(--card-dark); }
  .card--back { left: 620px; background: var(--card-light); }

  .spray-photo {
    position: absolute;
    left: 0; top: 40px;
    width: 300px; height: 160px;
    background: linear-gradient(90deg, #6a2a2e 0%, #8a3a6a 30%, #7a7a3a 55%, #1b7d7f 80%, var(--card-dark) 100%);
  }

  .brand {
    position: absolute;
    font-weight: 800;
    line-height: .95;
    text-transform: uppercase;
  }
  .brand__main { display: block; font-size: 64px; letter-spacing: 4px; }
  .brand__sub { display: block; font-size: 28px; letter-spacing: 1px; }
  .card--front .brand { right: 44px; top: 40px; color: var(--white); }

  .divider {
    position: absolute;
    height: 1px;
  }
  .card--front .divider { left: 215px; right: 30px; top: 190px; background: var(--rule-dark); }

  .person { position: absolute; }
  .card--front .person { left: 70px; top: 196px; }
  .person__name {
    color: var(--teal-light);
    font-size: 17px;
    font-weight: 500;
    text-transform: uppercase;
    letter-spacing: .3px;
  }
  .person__role { font-size: 13px; margin-top: 1px; }
  .card--front .person__role { color: var(--grey-text); }
  .contact { list-style: none; margin-top: 12px; }
  .contact__item {
    display: flex;
    align-items: center;
    gap: 8px;
    font-size: 13px;
    line-height: 19px;
  }
  .card--front .contact__item { color: var(--white); }
  .contact__item svg { width: 13px; height: 13px; flex: none; }
  .contact__accent { color: var(--teal-light); }

  .address {
    position: absolute;
    font-size: 12.5px;
    line-height: 17px;
    text-align: right;
    font-style: normal;
  }
  .card--front .address { right: 34px; top: 205px; color: var(--grey-text); }

  /* Back: light card with raised name and contact details */
  .card--back .brand {
    left: 50%; top: 28px;
    transform: translateX(-50%);
    color: var(--emboss);
    text-align: center;
  }
  .card--back .divider { left: 30px; right: 30px; top: 182px; background: var(--rule-light); }
  .card--back .person { left: 40px; top: 196px; }
  .card--back .person__name { color: var(--teal); }
  .card--back .person__role { color: var(--ink-soft); }
  .card--back .contact__item { color: var(--ink); }
  .card--back .contact__accent { color: var(--teal); }
  .card--back .address { right: 34px; top: 205px; color: var(--ink-soft); }
</style>
</head>
<body>

  <section class="card card--front" aria-label="Card front">
    <div class="spray-photo" role="img" aria-label="Photo of a hand holding a paint spray gun releasing a multicoloured mist"></div>

    <h1 class="brand">
      <span class="brand__main">VOR</span>
      <span class="brand__sub">Exterior</span>
      <span class="brand__sub">Coatings</span>
    </h1>

    <div class="divider"></div>

    <div class="person">
      <p class="person__name">Daniel Reyes</p>
      <p class="person__role">Managing Director</p>
      <ul class="contact">
        <li class="contact__item">
          <svg viewBox="0 0 14 14" fill="none" stroke="var(--teal-light)" stroke-width="1.2"><rect x="1" y="1" width="12" height="12" rx="1.5"/><path d="M4.5 3.5c-.6 2.8 1.5 6 5 7l.8-1.6-1.6-.9-.8.8c-1.1-.5-2-1.5-2.4-2.6l.8-.7-.8-1.7z"/></svg>
          044-987 654 321
        </li>
        <li class="contact__item">
          <svg viewBox="0 0 14 14" fill="none" stroke="var(--teal-light)" stroke-width="1.2"><rect x="1" y="3" width="12" height="8.5"/><path d="M1 3l6 5 6-5M1 11.5l4.5-4M13 11.5l-4.5-4"/></svg>
          info@vorcoatings.com
        </li>
        <li class="contact__item">
          <svg viewBox="0 0 14 14" fill="none" stroke="var(--teal-light)" stroke-width="1.1"><circle cx="7" cy="7" r="6"/><ellipse cx="7" cy="7" rx="2.6" ry="6"/><path d="M1 7h12M2 4h10M2 10h10"/></svg>
          <span>www.<span class="contact__accent">vorcoatings</span>.com</span>
        </li>
      </ul>
    </div>

    <address class="address">
      88, Harbor Road<br>
      Northfield, 30218
    </address>
  </section>

  <section class="card card--back" aria-label="Card back">
    <p class="brand">
      <span class="brand__main">VOR</span>
      <span class="brand__sub">Exterior</span>
      <span class="brand__sub">Coatings</span>
    </p>

    <div class="divider"></div>

    <div class="person">
      <p class="person__name">Daniel Reyes</p>
      <p class="person__role">Managing Director</p>
      <ul class="contact">
        <li class="contact__item">
          <svg viewBox="0 0 14 14" fill="none" stroke="var(--teal)" stroke-width="1.2"><rect x="1" y="1" width="12" height="12" rx="1.5"/><path d="M4.5 3.5c-.6 2.8 1.5 6 5 7l.8-1.6-1.6-.9-.8.8c-1.1-.5-2-1.5-2.4-2.6l.8-.7-.8-1.7z"/></svg>
          044-987 654 321
        </li>
        <li class="contact__item">
          <svg viewBox="0 0 14 14" fill="none" stroke="var(--teal)" stroke-width="1.2"><rect x="1" y="3" width="12" height="8.5"/><path d="M1 3l6 5 6-5M1 11.5l4.5-4M13 11.5l-4.5-4"/></svg>
          info@vorcoatings.com
        </li>
        <li class="contact__item">
          <svg viewBox="0 0 14 14" fill="none" stroke="var(--teal)" stroke-width="1.1"><circle cx="7" cy="7" r="6"/><ellipse cx="7" cy="7" rx="2.6" ry="6"/><path d="M1 7h12M2 4h10M2 10h10"/></svg>
          <span>www.<span class="contact__accent">vorcoatings</span>.com</span>
        </li>
      </ul>
    </div>

    <address class="address">
      88, Harbor Road<br>
      Northfield, 30218
    </address>
  </section>

</body>
</html>
```